Garlic Farm for Farm Sales/Restaurant sales

Need a professional, but appealing to agriculture world. We are selling 27 kinds of Organic Garlic from a farm in Simla,CO. I have uploaded logo and business information-we are going to need a template, because I will need to use it for four separate people.
-We are trying to appeal to Farm to table restaurants
-As well as growers/farmers

Target Market(s)

Agriculture Sales/Restaurants-Organic

Industry/Entity Type

Agriculture

Contact Information for Business Card

Want it to look more unique then your average kelto stock card- I want it to look amazing

Font styles to use
Sans Serif

Colors
0455a3
ec1f27
fbed22
ffffff

Requirements
Must have
• Just be creative
Nice to have
• Colorful
Should not have
• plain

```html
<!DOCTYPE html>
<html lang="en">
<head>
<meta charset="utf-8">
<title>Prairie Bulb Farm – Business Card</title>
<link href="https://fonts.googleapis.com/css2?family=Open+Sans:wght@400;600;700&display=swap" rel="stylesheet">
<style>
  :root {
    --navy: #0a2d5c;
    --red: #c8102e;
    --yellow: #fbed22;
    --white: #ffffff;
    --ink: #555a60;
    --backdrop: #ece9e4;
  }
  * { margin: 0; padding: 0; box-sizing: border-box; }
  html, body { width: 1200px; height: 987px; overflow: hidden; }
  body {
    background: var(--backdrop);
    font-family: "Open Sans", Arial, sans-serif;
    position: relative;
  }
  .card {
    position: absolute;
    left: 293px;
    width: 615px;
    height: 350px;
    box-shadow: 0 2px 6px rgba(0,0,0,.25);
    overflow: hidden;
  }
  .card--front { top: 131px; background: var(--white); }
  .card--back { top: 506px; background: var(--navy); }

  .brand {
    position: absolute;
    left: 0; right: 0;
    display: flex;
    flex-direction: column;
    align-items: center;
  }
  .brand__mark {
    border-radius: 50%;
    background: var(--red);
  }
  .brand__name {
    font-weight: 700;
    letter-spacing: .5px;
  }
  .card--front .brand { top: 20px; }
  .card--front .brand__mark { width: 88px; height: 88px; }
  .card--front .brand__name { color: var(--navy); font-size: 28px; margin-top: 14px; }

  .card--back .brand { top: 96px; }
  .card--back .brand__mark { width: 152px; height: 152px; }
  .card--back .brand__name { color: var(--white); font-size: 20px; margin-top: 14px; }

  .divider {
    position: absolute;
    left: 26px; right: 29px; top: 224px;
    height: 1px; background: var(--navy);
  }
  .person { position: absolute; left: 26px; top: 236px; }
  .person__name { color: var(--navy); font-weight: 700; font-size: 21px; line-height: 26px; }
  .person__role { color: var(--red); font-size: 16px; line-height: 22px; }
  .person__email { color: var(--ink); font-size: 16px; line-height: 30px; }

  .contact {
    position: absolute; right: 28px; top: 238px;
    list-style: none; text-align: right;
    color: var(--ink); font-size: 15.5px; line-height: 23px;
  }
  .contact li { display: flex; justify-content: flex-end; align-items: center; gap: 6px; }
  .contact svg { width: 15px; height: 15px; fill: var(--navy); }
  .contact .address { padding-right: 0; margin-top: 2px; }

  .base-rule { position: absolute; left: 0; right: 0; top: 319px; height: 2px; background: var(--red); }
  .base-band { position: absolute; left: 0; right: 0; top: 326px; bottom: 0; background: var(--navy); }

  .social {
    position: absolute; left: 102px; right: 140px; top: 294px;
    display: flex; align-items: center; gap: 4px;
  }
  .social__line { flex: 1; height: 1px; background: rgba(255,255,255,.7); }
  .social__dot {
    width: 22px; height: 22px; border-radius: 50%;
    border: 1.5px solid var(--white);
  }
</style>
</head>
<body>

<section class="card card--front">
  <div class="brand">
    <span class="brand__mark"></span>
    <span class="brand__name">Prairie Bulb Farm</span>
  </div>

  <div class="divider"></div>

  <div class="person">
    <p class="person__name">DALE MORROW</p>
    <p class="person__role">CEO/FOUNDER</p>
    <p class="person__email">dale@prairiebulb.com</p>
  </div>

  <ul class="contact">
    <li>719-555-0148
      <svg viewBox="0 0 24 24" aria-hidden="true"><path d="M6.6 10.8a15.1 15.1 0 0 0 6.6 6.6l2.2-2.2c.3-.3.7-.4 1-.2 1.1.4 2.3.6 3.6.6.6 0 1 .4 1 1V20c0 .6-.4 1-1 1A17 17 0 0 1 3 4c0-.6.4-1 1-1h3.5c.6 0 1 .4 1 1 0 1.3.2 2.5.6 3.6.1.3 0 .7-.2 1z"/></svg>
    </li>
    <li>www.PrairieBulb.com
      <svg viewBox="0 0 24 24" aria-hidden="true"><path d="M12 2a10 10 0 1 0 0 20 10 10 0 0 0 0-20zm-1 17.9A8 8 0 0 1 4.1 10l4.9 5v1c0 1.1.9 2 2 2zm6.9-2.5A2 2 0 0 0 16 16h-1v-3c0-.6-.4-1-1-1H8v-2h2c.6 0 1-.4 1-1V7h2c1.1 0 2-.9 2-2v-.4a8 8 0 0 1 2.9 12.8z"/></svg>
    </li>
    <li class="address">P.O. Box 12 Larkfield, CO&nbsp; 80800</li>
  </ul>

  <div class="base-rule"></div>
  <div class="base-band"></div>
</section>

<section class="card card--back">
  <div class="brand">
    <span class="brand__mark"></span>
    <span class="brand__name">Prairie Bulb Farm</span>
  </div>

  <div class="social">
    <span class="social__line"></span>
    <span class="social__dot"></span>
    <span class="social__dot"></span>
    <span class="social__dot"></span>
    <span class="social__dot"></span>
    <span class="social__line"></span>
  </div>
</section>

</body>
</html>
```